Tellmora Corporate Stationery

Look for design of all new corporate stationery for an existing insurance broking business that is going through a redesign and move from older partners to younger family members. New Logo is attached. Company is Brisbane based.
Colours in the Logo is Hex #43bed8 and website features a lot of hex #17b8d8. Website front page "A plan to protect you" - headline. "Professional and Individual advice to protect your greatest assets" - tagline.

Stationery required: Business Cards, Letter head, Thank-you cards, Birthday cards, Presentation folders, With Compliment slips and a powerpoint template. We also would like to send a card to all customers with the something along of the lines of "something new".

Target Market(s)

Customers of Insurance business looking at superannuation, life and income protection insurance, investment advice and wills

Industry/Entity Type

Insurance Broker

Font styles to use
Other font styles liked:
• same as logo

Requirements
Must have
• The above designs for new stationery for the new business including:
• Business Cards, Letter head, Thank-you cards, Birthday cards, Presentation folders, With Compliment slips and a powerpoint template. We also would like to send a card to all customers with the something along of the lines of "something new".
Nice to have
• It is a new look - long time family business being passed to next generation - big focus on advice for YOU, individual advice etc..

```html
<!DOCTYPE html>
<html lang="en">
<head>
<meta charset="utf-8">
<title>Tellmora Financial Group – A Plan to Protect You</title>
<link rel="stylesheet" href="https://fonts.googleapis.com/css2?family=Roboto+Condensed:wght@700&family=Roboto:wght@300;400;500&family=Cabin:wght@400&display=swap">
<style>
  :root {
    --page-bg: #d9d9d9;
    --slide-bg: #231f20;
    --slide-bg-light: #2a2627;
    --brand-cyan: #43bed8;
    --band-teal: #1d6675;
    --text-white: #ffffff;
    --text-soft: #e6e6e6;
  }
  * { margin: 0; padding: 0; box-sizing: border-box; }
  html, body {
    width: 1200px; height: 1200px; overflow: hidden;
    background: var(--page-bg);
  }
  .slide {
    position: absolute; left: 0; top: 263px;
    width: 1200px; height: 674px;
    background:
      repeating-linear-gradient(90deg, rgba(255,255,255,0.012) 0 2px, rgba(0,0,0,0.02) 2px 5px),
      linear-gradient(180deg, var(--slide-bg-light), var(--slide-bg) 60%);
    color: var(--text-white);
    font-family: "Roboto", sans-serif;
    text-align: center;
  }
  .brand { position: absolute; left: 0; right: 0; top: 22px; }
  .brand-mark { display: block; margin: 0 auto; }
  .brand-name {
    margin-top: 10px;
    font-family: "Roboto", sans-serif; font-weight: 500;
    font-size: 38px; letter-spacing: 3px; line-height: 1;
    color: var(--text-white);
  }
  .brand-sub {
    margin-top: 4px; font-weight: 500; font-size: 17px;
    letter-spacing: 1.5px; line-height: 1;
  }
  .brand-url {
    margin-top: 4px; font-weight: 400; font-size: 12px;
    letter-spacing: 1.5px; line-height: 1;
  }
  .headline {
    position: absolute; left: 0; right: 0; top: 280px;
    font-family: "Roboto Condensed", sans-serif; font-weight: 700;
    font-size: 64px; line-height: 1; color: var(--brand-cyan);
    letter-spacing: 0.5px;
  }
  .tagline {
    position: absolute; left: 0; right: 0; top: 352px;
    font-size: 18px; font-weight: 400; color: var(--text-white);
  }
  .intro {
    position: absolute; left: 150px; right: 150px; top: 416px;
    font-size: 16px; font-weight: 300; line-height: 27px;
    color: var(--text-soft);
  }
  .contact-line {
    position: absolute; left: 0; right: 0; top: 611px;
    font-family: "Cabin", sans-serif; font-size: 12.5px; color: var(--text-white);
  }
  .licence-band {
    position: absolute; left: 0; right: 0; bottom: 0; height: 41px;
    background: var(--band-teal);
    font-family: "Cabin", sans-serif; font-size: 17px; letter-spacing: 1px;
    line-height: 41px; color: var(--text-white);
  }
</style>
</head>
<body>
  <main class="slide">
    <header class="brand">
      <svg class="brand-mark" width="56" height="56" viewBox="0 0 56 56" aria-hidden="true">
        <circle cx="28" cy="28" r="26" fill="none" stroke="var(--text-white)" stroke-width="4"/>
      </svg>
      <div class="brand-name">TELLMORA</div>
      <div class="brand-sub">FINANCIAL GROUP</div>
      <div class="brand-url">www.tellmorafinancial.com</div>
    </header>

    <h1 class="headline">A PLAN TO PROTECT YOU</h1>
    <p class="tagline">Professional &amp; Individual advice to protect your greatest assets</p>

    <p class="intro">
      Lorem Ipsum has been the industry's standard dummy text ever since the 1500s, when an unknown printer took a<br>
      galley of type and scrambled it to make a type specimen book. It has survived not only five centuriesbut also the leap<br>
      into electronic typesetting, remaining essentially unchanged. It was popularised in the 1960s with the release of Tra-<br>
      cefold sheets containing Lorem Ipsum passages, and more recently with desktop publishing software<br>
      like Quillset Layout including versions of Lorem Ipsum
    </p>

    <p class="contact-line">T: 1-555-018244 | E: mia@tellmorafinancial.com | Dummy city, Dummy Country Land</p>

    <footer class="licence-band">Authorised Representatives of Norvane AFS Licence No 417206</footer>
  </main>
</body>
</html>
```